Clear Plastic Card Design

I am looking to have a business card designed from my logo icon. I am looking to match the style of a different business card I have attached in the files.
Looking for a card that is plastic, with layers of transparency in the shape of my logo icon (also attached in the files) - not a circle like the other card. The winning design will incorporate the red icon logo on the front and back and include the charity's name, "Light for the Weary Souls" in the same or similar font, as well as an email and phone number. For now, use the email: email@lightfortheweary-mail.org and the phone number 555-382-7194.
We like how the sample business card has transparency, partial and full opacity layers and a matching color scheme. Files will need to be in vector so that our business card printing company can work with it.
UPDATE:
We've some excellent designs in, thank you everyone! I got an early review from the owner, and he requested a minor redirect to find his perfect design. He wants the design to stand out by NOT being a rectangle. Try instead a circle, square, or best yet - something that falls in the outline of the logo icon, either fully or partially. Thank you, everyone!
Light for the Weary Souls text should be incorporated as well as a phone and email.

```html
<!DOCTYPE html>
<html lang="en">
<head>
<meta charset="utf-8">
<title>Light for the Weary Souls – Business Card</title>
<link rel="stylesheet" href="https://fonts.googleapis.com/css2?family=Lexend:wght@400&family=Arimo:wght@400;700&display=swap">
<style>
  :root {
    --backdrop: #e7e4e2;
    --card-surface: #f3f2f1;
    --card-edge: #d2cfcd;
    --brand-red: #b5161a;
    --brand-red-deep: #9c0d10;
    --ink-dark: #3a3a3a;
    --ink-grey: #4a4a4a;
    --swoosh: #111111;
    --contact-ink: #ffffff;
  }
  * { margin: 0; padding: 0; box-sizing: border-box; }
  html, body {
    width: 1200px;
    height: 1011px;
    overflow: hidden;
    background: var(--backdrop);
  }
  .stage {
    width: 1200px;
    height: 1011px;
    display: flex;
    align-items: center;
    justify-content: center;
  }
  .card { width: 880px; height: 880px; display: block; }
  .org-name { font-family: "Lexend", sans-serif; font-weight: 400; font-size: 62px; fill: var(--ink-dark); }
  .person-name { font-family: "Arimo", sans-serif; font-weight: 700; font-size: 50px; fill: var(--brand-red); letter-spacing: 1px; }
  .person-title { font-family: "Arimo", sans-serif; font-weight: 400; font-size: 30px; fill: var(--ink-grey); letter-spacing: 1px; }
  .contact-line { font-family: "Arimo", sans-serif; font-weight: 400; font-size: 29px; fill: var(--contact-ink); }
  .contact-icon { fill: none; stroke: var(--contact-ink); stroke-width: 2.2; stroke-linecap: round; stroke-linejoin: round; }
</style>
</head>
<body>
<main class="stage">
  <svg class="card" viewBox="-10 -10 880 880" xmlns="http://www.w3.org/2000/svg" aria-label="Round clear business card for Light for the Weary Souls">
    <defs>
      <clipPath id="card-shape"><circle cx="430" cy="430" r="430"/></clipPath>
      <linearGradient id="band-fill" x1="0" y1="0" x2="1" y2="0">
        <stop offset="0" stop-color="#bf4a4c"/>
        <stop offset="0.45" stop-color="var(--brand-red)"/>
        <stop offset="1" stop-color="var(--brand-red-deep)"/>
      </linearGradient>
      <radialGradient id="texture-fill" cx="0.5" cy="0.5" r="0.5">
        <stop offset="0" stop-color="#9a9896" stop-opacity="0.55"/>
        <stop offset="1" stop-color="#cfcdcb" stop-opacity="0"/>
      </radialGradient>
    </defs>

    <circle class="card-body" cx="430" cy="430" r="430" fill="var(--card-surface)" stroke="var(--card-edge)" stroke-width="3"/>

    <g clip-path="url(#card-shape)">
      <ellipse class="brush-texture" role="img" aria-label="Soft smoky brush texture" cx="330" cy="330" rx="260" ry="300" fill="url(#texture-fill)"/>

      <path class="contact-band" d="M0 700 C 200 600, 420 555, 880 595 L 880 880 L 0 880 Z" fill="url(#band-fill)"/>
      <path class="swoosh" d="M280 598 C 420 560, 600 530, 835 566 L 828 592 C 620 560, 430 570, 280 598 Z" fill="var(--swoosh)"/>
    </g>

    <circle class="brand-dot" cx="575" cy="210" r="115" fill="var(--brand-red)"/>

    <text class="org-name" x="89" y="353">Light for the</text>
    <text class="org-name" x="89" y="414">Weary Souls</text>

    <text class="person-name" x="89" y="502">DANIEL HARPER</text>
    <text class="person-title" x="91" y="543">Founder &amp; CEO</text>

    <text class="contact-line" x="620" y="665" text-anchor="end">555-382-7194</text>
    <text class="contact-line" x="620" y="709" text-anchor="end">email@lightfortheweary-mail.org</text>
    <text class="contact-line" x="620" y="751" text-anchor="end">lightfortheweary.org</text>

    <g class="contact-icon phone-icon" transform="translate(636 642)">
      <path d="M4 3 L9 2 L11 8 L8 10 C9 13 11 15 14 16 L16 13 L22 15 L21 20 C12 21 3 12 4 3 Z"/>
    </g>
    <g class="contact-icon mail-icon" transform="translate(636 690)">
      <rect x="1" y="2" width="22" height="15"/>
      <path d="M1 2 L12 11 L23 2"/>
    </g>
    <g class="contact-icon web-icon" transform="translate(636 730)">
      <circle cx="12" cy="12" r="10"/>
      <path d="M2 12 H22 M12 2 C7 7 7 17 12 22 M12 2 C17 7 17 17 12 22"/>
    </g>
  </svg>
</main>
</body>
</html>
```